Alloy wheel repair business needs a website

Install logo previously purchased from makerhive, toolbar with dropdowns. services, gallery, clients , contact ect
Maybe mission statment

Target Market(s)

vehicle owners, auto dealers,insurance companies,

Industry/Entity Type

Alloy Wheel Repair

Coding

Coded - Design and coding required

Number of Pages Required

4 page

Font styles to use
Sans Serif

Colors
0054AA
0677BA
7BADD7
CADEEF
E8F1F8

```html
<!DOCTYPE html>
<html lang="en">
<head>
<meta charset="utf-8">
<title>Rimcraft Works – Alloy Wheel Repair</title>
<link rel="stylesheet" href="https://fonts.googleapis.com/css2?family=Audiowide&family=Poppins:wght@400;500;600;700&display=swap">
<style>
:root{
  --navy:#0054AA;
  --blue:#0677BA;
  --brand:#3F86CC;
  --sky:#7BADD7;
  --mist:#CADEEF;
  --ice:#E8F1F8;
  --ink:#111111;
  --text:#333333;
  --white:#ffffff;
}
*{margin:0;padding:0;box-sizing:border-box}
html,body{width:1200px;height:3862px;overflow:hidden}
body{font-family:"Poppins",sans-serif;color:var(--text);background:var(--white);position:relative}
.abs{position:absolute}
.display{font-family:"Audiowide",sans-serif;letter-spacing:2px;text-transform:uppercase}

/* header */
.site-header{left:0;top:0;width:1200px;height:80px;background:var(--white)}
.logo{display:flex;align-items:center;gap:6px;font-weight:700;color:var(--brand);font-size:20px;letter-spacing:1px;white-space:nowrap}
.logo .dot{width:16px;height:16px;border-radius:50%;background:var(--brand);flex:none}
.site-header .logo{left:90px;top:28px;font-size:13px;letter-spacing:.5px;gap:5px}
.site-header .logo .dot{width:12px;height:12px}
.nav a{position:absolute;top:30px;font-size:16px;font-weight:600;color:#222;text-decoration:none;white-space:nowrap;transform:translateX(-50%)}
.nav a.active{color:var(--brand)}

/* hero */
.hero{left:0;top:80px;width:1200px;height:520px;background:linear-gradient(120deg,#1a1a1a 0%,#4a4a4a 35%,#2a2a2a 55%,#c96a1e 75%,#8d8a2a 90%,#333 100%)}
.hero-panel{left:180px;top:185px;width:840px;height:275px;background:rgba(50,50,50,.85);text-align:center}
.hero-title{position:absolute;left:0;right:0;font-size:44px;white-space:nowrap}
.btn{position:absolute;display:flex;align-items:center;justify-content:center;background:var(--brand);color:var(--white);font-weight:600;font-size:17px;text-transform:uppercase;white-space:nowrap}

/* mission */
.photo-frame{background:var(--white);box-shadow:0 2px 10px rgba(0,0,0,.2);padding:9px}
.photo-frame .fill,.fill{width:100%;height:100%}
.section-title{font-size:42px;color:var(--brand);white-space:nowrap}
.mission-text{left:600px;top:758px;width:486px;font-size:16.5px;line-height:30px;text-align:justify}

/* services */
.band{left:0;width:1200px;background:var(--ice)}
.service-card{top:1353px;width:223px;height:168px;background:var(--white);display:flex;align-items:center;justify-content:center}
.service-label{top:1548px;width:223px;text-align:center;font-size:16px;line-height:26px;font-weight:600;color:var(--brand)}

/* gallery */
.tile{overflow:hidden}
.arrow{width:30px;height:30px;border:1.5px solid #333;border-radius:50%;display:flex;align-items:center;justify-content:center}

/* testimonials */
.testimonial{background:var(--white)}
.testimonial.side{opacity:.35;box-shadow:0 2px 10px rgba(0,0,0,.08)}
.testimonial.main{box-shadow:0 4px 18px rgba(0,0,0,.15)}
.stars{color:#F2C200;letter-spacing:2px}
.avatar{border-radius:50%}
.dots span{display:inline-block;width:9px;height:9px;border-radius:50%;background:#999;margin:0 1px}

/* contact */
.contact{left:0;top:3035px;width:704px;height:485px;background:#4A8BD0}
.field{position:absolute;width:245px;height:62px;border:1px solid rgba(255,255,255,.8);color:var(--white);font-size:16px;padding:0 24px;display:flex;align-items:center}

/* footer */
.site-footer{left:0;top:3520px;width:1200px;height:342px;background:#141414}
.site-footer .logo{left:0;right:0;top:78px;justify-content:center;color:var(--white);font-size:24px}
.site-footer .logo .dot{background:var(--white)}
.foot-nav a{position:absolute;top:3690px;transform:translateX(-50%);color:var(--white);font-size:16px;font-weight:600;text-decoration:none;white-space:nowrap}
.social{width:24px;height:24px;border-radius:4px;background:var(--white)}
</style>
</head>
<body>

<header class="abs site-header">
  <div class="abs logo"><span class="dot"></span>RIMCRAFT WORKS</div>
  <nav class="nav">
    <a class="active" style="left:286px">HOME</a>
    <a style="left:445px">OUR MISSION</a>
    <a style="left:622px">SERVICES</a>
    <a style="left:776px">GALLERY</a>
    <a style="left:924px">CLIENTS</a>
    <a style="left:1091px">CONTACT US</a>
  </nav>
</header>

<section class="abs hero" role="img" aria-label="Showroom wall of chrome and coloured alloy wheels"></section>
<div class="abs hero-panel">
  <h1 class="display hero-title" style="top:45px;color:var(--white)">Welcome to</h1>
  <h1 class="display hero-title" style="top:97px;color:var(--brand)">Rimcraft Works</h1>
  <a class="btn" style="left:335px;top:178px;width:172px;height:58px">Get Started</a>
</div>

<!-- mission -->
<div class="abs photo-frame" style="left:112px;top:690px;width:393px;height:357px">
  <div class="fill" role="img" aria-label="Black tyres and dark alloy wheel close-up" style="background:linear-gradient(135deg,#6a6a6a,#1c1c1c 60%,#3a3a3a)"></div>
</div>
<div class="abs photo-frame" style="left:39px;top:866px;width:248px;height:235px;padding:9px 9px 0 9px;box-shadow:none;background:var(--white)">
  <div class="fill" role="img" aria-label="Alloy wheel in a workshop" style="background:linear-gradient(120deg,#2b3d55,#8a8f98 45%,#c94a3a 80%,#6b2b2b)"></div>
</div>
<h2 class="abs display section-title" style="left:600px;top:683px">Our Mission</h2>
<p class="abs mission-text">Lorem ipsum dolor sit amet, consectetur adipiscing elit, sed do eiusmod tempor incididunt ut labore et dolore magna aliqua. Ut enim ad minim veniam, quis nostrud exercitation ullamco laboris nisi ut aliquip ex ea commodo consequat. Duis aute irure dolor in reprehenderit in voluptate velit esse cillum dolore eu fugiat nulla pariatur. Excepteur sint occaecat cupidatat non proident .</p>
<a class="btn" style="left:603px;top:1006px;width:170px;height:56px">Read More</a>

<!-- services -->
<section class="abs band" style="top:1155px;height:553px"></section>
<h2 class="abs display section-title" style="left:0;width:1200px;text-align:center;top:1250px">Services</h2>

<div class="abs service-card" style="left:115px">
  <svg width="90" height="90" viewBox="0 0 90 90"><circle cx="45" cy="45" r="42" fill="#1a1a1a"/><circle cx="45" cy="45" r="32" fill="#fff"/><g stroke="#1a1a1a" stroke-width="9" stroke-linecap="round"><line x1="45" y1="45" x2="45" y2="15"/><line x1="45" y1="45" x2="74" y2="54"/><line x1="45" y1="45" x2="63" y2="70"/><line x1="45" y1="45" x2="27" y2="70"/><line x1="45" y1="45" x2="16" y2="54"/></g><circle cx="45" cy="45" r="9" fill="#fff" stroke="#1a1a1a" stroke-width="5"/></svg>
</div>
<div class="abs service-card" style="left:366px">
  <svg width="90" height="90" viewBox="0 0 90 90"><circle cx="45" cy="45" r="40" fill="none" stroke="#1a1a1a" stroke-width="10" stroke-dasharray="8 5"/><circle cx="45" cy="45" r="32" fill="#1a1a1a"/><circle cx="45" cy="45" r="22" fill="#fff"/><g stroke="#1a1a1a" stroke-width="6"><line x1="45" y1="23" x2="45" y2="67"/><line x1="23" y1="45" x2="67" y2="45"/></g><circle cx="45" cy="45" r="7" fill="#1a1a1a"/></svg>
</div>
<div class="abs service-card" style="left:616px">
  <svg width="100" height="90" viewBox="0 0 100 90"><rect x="50" y="3" width="44" height="84" rx="6" fill="#1a1a1a"/><g stroke="#fff" stroke-width="3"><line x1="62" y1="3" x2="62" y2="87"/><line x1="74" y1="3" x2="74" y2="87"/><line x1="86" y1="3" x2="86" y2="87"/></g><circle cx="45" cy="45" r="42" fill="#1a1a1a"/><circle cx="45" cy="45" r="30" fill="#fff"/><g stroke="#1a1a1a" stroke-width="8"><line x1="45" y1="15" x2="45" y2="75"/><line x1="15" y1="45" x2="75" y2="45"/></g><circle cx="45" cy="45" r="9" fill="#1a1a1a"/></svg>
</div>
<div class="abs service-card" style="left:866px">
  <svg width="90" height="90" viewBox="0 0 90 90"><circle cx="45" cy="45" r="42" fill="#1a1a1a"/><g fill="#fff"><path d="M45 10 L55 30 L35 30Z"/><path d="M78 38 L62 52 L58 34Z"/><path d="M66 76 L47 64 L62 55Z"/><path d="M24 76 L28 55 L43 64Z"/><path d="M12 38 L32 34 L28 52Z"/></g><circle cx="45" cy="45" r="8" fill="#fff"/></svg>
</div>
<div class="abs service-label" style="left:115px">WHEEL REFINISHING</div>
<div class="abs service-label" style="left:366px">WHEEL<br>REMANUFACTURING</div>
<div class="abs service-label" style="left:616px">WHEEL<br>STRAIGHTENING</div>
<div class="abs service-label" style="left:866px">CRACKED<br>WHEEL REPAIR</div>

<!-- gallery -->
<h2 class="abs display section-title" style="left:0;width:1200px;text-align:center;top:1805px">Gallery</h2>
<div class="abs tile" role="img" aria-label="Technician fitting a tyre on an alloy wheel" style="left:116px;top:1927px;width:231px;height:186px;background:linear-gradient(135deg,#222,#6d6d6d 55%,#b23a2a)"></div>
<div class="abs tile" role="img" aria-label="Mechanic showing a wheel to a customer" style="left:363px;top:1927px;width:231px;height:186px;background:linear-gradient(135deg,#e8e8e8,#b9a88a 50%,#3a3a3a)"></div>
<div class="abs tile" role="img" aria-label="Silver alloy wheel mounted on a balancing machine" style="left:608px;top:1927px;width:230px;height:186px;background:linear-gradient(135deg,#3a4a66,#cfcfcf 55%,#4a4a4a)"></div>
<div class="abs tile" role="img" aria-label="Spray painting a black alloy wheel" style="left:853px;top:1927px;width:231px;height:391px;background:linear-gradient(180deg,#d8d8d8,#9a9ea6 40%,#2a2a2a 75%,#141414)"></div>
<div class="abs tile" role="img" aria-label="Gloved hands working on a bronze alloy wheel" style="left:115px;top:2133px;width:479px;height:185px;background:linear-gradient(100deg,#1a1a1a,#5a4a3a 40%,#b07a3a 65%,#2a2a2a)"></div>
<div class="abs tile" role="img" aria-label="Washing a car wheel with a pressure hose" style="left:606px;top:2133px;width:231px;height:185px;background:linear-gradient(135deg,#f2f2f2,#9aa3b0 50%,#c0601e)"></div>
<div class="abs arrow" style="left:43px;top:2108px"><svg width="10" height="14" viewBox="0 0 10 14"><path d="M8 1 L2 7 L8 13" fill="none" stroke="#333" stroke-width="1.5"/></svg></div>
<div class="abs arrow" style="left:1127px;top:2108px"><svg width="10" height="14" viewBox="0 0 10 14"><path d="M2 1 L8 7 L2 13" fill="none" stroke="#333" stroke-width="1.5"/></svg></div>

<!-- testimonials -->
<section class="abs band" style="top:2455px;height:580px"></section>
<h2 class="abs display" style="left:0;width:1200px;text-align:center;top:2537px;font-size:42px;color:var(--ink)">Testimonials</h2>

<div class="abs testimonial side" style="left:113px;top:2680px;width:230px;height:188px">
  <div class="stars abs" style="left:160px;top:12px;font-size:13px">★★★★</div>
  <p class="abs" style="left:34px;top:38px;width:180px;font-size:11px;line-height:22px">Sed ut perspiciatis unde omnis luptatem accusantium dolore rem aperiam, eaque ipsa quae</p>
  <div class="abs avatar" role="img" aria-label="Customer portrait" style="left:24px;top:120px;width:54px;height:54px;background:#d9c2ad"></div>
  <div class="abs" style="left:105px;top:140px;font-size:10px;font-weight:600">ELIAN</div>
</div>
<div class="abs testimonial side" style="left:860px;top:2680px;width:228px;height:188px">
  <div class="stars abs" style="left:12px;top:10px;font-size:13px">★★★★</div>
  <p class="abs" style="left:10px;top:34px;width:200px;font-size:11px;line-height:22px">unde omnis iste natus error sit ntium doloremque laudantium, eaque ipsa quae ab illo inventore</p>
  <div class="abs" style="left:45px;top:142px;font-size:10px;font-weight:600">MARCO HALE</div>
  <div class="abs avatar" role="img" aria-label="Customer portrait" style="left:148px;top:120px;width:54px;height:54px;background:#c9b6a6"></div>
</div>
<div class="abs testimonial main" style="left:326px;top:2642px;width:544px;height:258px">
  <div class="stars abs" style="left:0;right:0;text-align:center;top:18px;font-size:22px">★★★★★</div>
  <p class="abs" style="left:37px;top:54px;width:476px;font-size:16px;line-height:30px;text-align:justify">Sed ut perspiciatis unde omnis iste natus error sit voluptatem accusantium doloremque laudantium, totam rem aperiam, eaque ipsa</p>
  <div class="abs avatar" role="img" aria-label="Customer portrait" style="left:36px;top:150px;width:76px;height:76px;background:linear-gradient(135deg,#c98a6a,#8a5a4a)"></div>
  <div class="abs" style="left:146px;top:180px;font-size:13px;font-weight:700;color:var(--ink)">- DANA ROSS</div>
</div>
<div class="abs dots" style="left:0;width:1200px;text-align:center;top:2945px"><span></span><span></span><span></span></div>

<!-- contact -->
<section class="abs contact">
  <h2 class="abs display" style="left:138px;top:100px;font-size:42px;color:var(--white);white-space:nowrap">Get in Touch</h2>
  <div class="field" style="left:139px;top:190px">First Name</div>
  <div class="field" style="left:392px;top:190px">Last Name</div>
  <div class="field" style="left:139px;top:259px">Email</div>
  <div class="field" style="left:392px;top:259px">Phone</div>
  <a class="abs" style="left:139px;top:363px;width:154px;height:49px;background:var(--white);color:var(--navy);font-weight:700;font-size:15px;display:flex;align-items:center;justify-content:center">SUBMIT</a>
</section>
<div class="abs" role="img" aria-label="Black and white stack of alloy wheels" style="left:704px;top:3035px;width:496px;height:485px;background:radial-gradient(circle at 65% 55%,#9a9a9a,#2a2a2a 55%,#0d0d0d)"></div>

<!-- footer -->
<footer class="abs site-footer">
  <div class="abs logo"><span class="dot"></span>RIMCRAFT WORKS</div>
</footer>
<nav class="foot-nav">
  <a style="left:183px">HOME</a>
  <a style="left:342px">OUR MISSION</a>
  <a style="left:519px">SERVICES</a>
  <a style="left:674px">GALLERY</a>
  <a style="left:821px">CLIENTS</a>
  <a style="left:984px">CONTACT US</a>
</nav>
<div class="abs social" style="left:533px;top:3744px"></div>
<div class="abs social" style="left:572px;top:3744px"></div>
<div class="abs social" style="left:611px;top:3744px"></div>
<div class="abs social" style="left:649px;top:3744px"></div>
<div class="abs" style="left:115px;top:3810px;width:973px;height:1px;background:#888"></div>
<p class="abs" style="left:0;width:1200px;text-align:center;top:3827px;font-size:13px;color:var(--white)">© 2023rimcraftworks. All Rights Reserved.</p>

</body>
</html>
```